Commercial Real Estate Corporate Site

Our company sells an ERP software to Commercial Real Estate Companies, this project is part of a marketing and sales relaunch of the company.

See attached for PDF formatted Design brief

The software is a modular system where client’s can adopt one module at a time. Our customers are corporate clients who own between 10M and 10B of real estate properties. The typical customer is from the IT or the Financial arm of the company. Our differentiation in the market is that our system is built on a no-code environment, so making changes for the client is quick. Incumbents in the market have long implementation cycles, and customization is often not possible. Competitors are Quorvel, TKB, PlotNest, Vumora.

We need a design for our site which will be implemented into Brevo Forge. **All designs must be compatible with the newest version of Brevo Forge.**

We have produced the following attached assets to use in the website design.:

1. Logo
2. Brand Guidelines
3. Content for Pages
4. Menu Structures
5. Illustrations (modules)
I can't attach them because the files are too big, so they're in this google drive instead:
https://files.examplestore.net/share/k29Xa7Lq0Pz3Rt8MwB5nYc4Hv1Jd6Fe?mode=view

The mechanic for our sales process is as follows:

1. We find on module from our application that a client is interested in. The illustrations that we’ve attached represent the individual modules (elements) of the software.
1. For instance, one of our current customers has purchased a commissions module from us which helps calculate the commission that brokers receive for buying and selling their properties.
2. We provide immense value through the module, and then keep in sales communication with the client to determine which other modules we can implement for them.
1. For instance, in the example above, the client is so happy with the commissions module that they want to start working with our leasing module as well. In the next business quarter, they also choose to add our financials module to their business systems.

### Logo

Attached

### Brand Guidelines

Attached

We are open to suggestions on the secondary colour palette.

### **Site Copy**

**We require the following pages to be created; For now, we will do one Market Page, one Product Page, and one Platform / Services Page, and we will use those as inspiration to create the other dozen Marketing Pages and 30 or so Product Pages.**

**Homepage**

Attached

**Market Page** - look at the quorvel site under the Office, Industrial, Retail (https://www.quorvel.com/products/quorvel-commercial-suite/)

**Product** - One product provided, but there will be 30 - look at the vumora page

(https://www.vumora.com/products/general-accounting)

**Platform / Services Page** - pages that tell the story of our platform and services, content to be provided - the platform will use our modules as it highlights the story of the configurability and composability of the platform. Instead of the icons that they use, we want to use our modules.

- https://www.pelbrix.com/enterprise-applications-platform
- https://www.pelbrix.com/cloud-architecture

**Team Page** - just add sample content for starters (6 Team Members to start)

**Schedule Demo Page** - the call to action for all pages

(https://go.vumora.com/schedule-demo.html)

### Menu Structure

The menu is provided as an attachment.

### Illustrations Information

A note about the illustrations - we have provided an illustrator file with the modules, and if you’d like you can arrange the in any way that you’d like to. We especially like when the modules are positioned like a periodic table of the elements.

Our existing clients are

- Torvane Coop - https://www.torvanecoop.com/real-estate/
- Dalsworth Realestate https://dalsworth.com

Our competitors are

- Quorvel - www.quorvel.com
- TKB - [www.tkbsoftware.com](https://www.tkbsoftware.com/) (we don’t like how this one looks)
- Vumora - www.vumora.com
- Plotnest - www.plotnest.com

Design inspiration

- https://lark-studio.brevosite.com/velmo
- Corporate
- Established
- Modern

### Stock Images Guidance

- https://www.drafta.net/design/QXR7Lm2TpWz/Hk9vN3c8Yd41-FbqsaZRr/edit?utm_content=QXR7Lm2TpWz&utm_campaign=designshare&utm_medium=link2&utm_source=sharebutton

Target Market(s)

Commercial Real Estate Companies - they typically own a portfolio of 50 - 5000 real estate properties and need a software to manage it all.

Coding

Coded - Design and coding required

Number of Pages Required

5+ page

Font styles to use
Other font styles liked:
• Fonts defined in brand guideline

Requirements
Must have
• Brevo Forge, Use the Elemental Design, Download ai.zip and png.zip Use Brand Guideline,
Nice to have
• Check design breif

```html
<!DOCTYPE html>
<html lang="en">
<head>
<meta charset="utf-8">
<title>Trelvix — Enterprise Applications Platform for Real Estate</title>
<link href="https://fonts.googleapis.com/css2?family=Montserrat:wght@500;600;700;800&family=Roboto:wght@400;500;700&display=swap" rel="stylesheet">
<style>
:root{
  --red:#e30b0b;
  --red-dark:#c90808;
  --gold:#d6a351;
  --ink:#222222;
  --text:#3a3a3a;
  --pink:#fcf0ef;
  --beige:#f8f1e8;
  --footer:#2b2b2b;
  --white:#ffffff;
}
*{margin:0;padding:0;box-sizing:border-box}
html,body{width:1200px;height:3655px;overflow:hidden}
body{font-family:'Roboto',sans-serif;color:var(--text);background:var(--white);position:relative}
.abs{position:absolute}
h2.section-title{font-family:'Montserrat',sans-serif;font-weight:700;font-size:34px;color:var(--ink);text-align:center;text-transform:uppercase;letter-spacing:.3px}
.rule{width:46px;height:3px;background:var(--red);margin:0 auto}
.tagline{font-size:15px;color:var(--gold);font-weight:500;text-align:center}
.body-copy{font-size:15px;line-height:27px;text-align:justify}
.body-copy p+p{margin-top:14px}

/* top bar */
.topbar{left:0;top:0;width:1200px;height:44px;background:var(--red);color:var(--white);font-size:12.5px;font-weight:700}
.topbar span{position:absolute;top:14px;display:flex;align-items:center;gap:10px}
.topbar svg{width:12px;height:12px;fill:var(--white)}

/* nav */
.nav{left:0;top:44px;width:1200px;height:88px;background:var(--white);border-bottom:1px solid #eee}
.brand{left:110px;top:20px;display:flex;align-items:center;gap:10px}
.brand-mark{width:40px;height:40px;background:var(--red)}
.brand-name{font-family:'Montserrat',sans-serif;font-weight:800;font-size:30px;color:var(--red);letter-spacing:1px}
.menu{left:329px;top:36px;display:flex;gap:27px;font-size:15px;font-weight:700;color:#222;text-transform:uppercase;font-family:'Roboto',sans-serif}

/* hero */
.hero{left:0;top:132px;width:1200px;height:613px;background:radial-gradient(ellipse at 78% 45%,#1d5a86 0%,#0d2b44 35%,#071522 70%,#04090f 100%)}
.hero-welcome{left:107px;top:238px;font-family:'Montserrat',sans-serif;font-weight:700;font-size:31px;color:var(--gold)}
.hero-title{left:101px;top:284px;font-family:'Montserrat',sans-serif;font-weight:700;font-size:74px;color:var(--white);letter-spacing:1px}
.hero-sub{left:107px;top:378px;width:450px;font-size:18.5px;line-height:27px;font-weight:700;color:var(--white)}
.btn{display:inline-flex;align-items:center;gap:10px;border-radius:24px;color:var(--white);font-weight:700;font-size:13px;text-transform:uppercase}
.btn svg{width:13px;height:13px}
.hero-btn{left:107px;top:455px;height:45px;padding:0 20px;background:var(--red)}

/* about */
.about{left:0;top:745px;width:1200px;height:601px;background:var(--pink)}
.about-art{left:110px;top:818px;width:455px;height:437px;background:linear-gradient(135deg,#f6d6d4,#f0c2bf);border-radius:6px}
.about-text{left:611px;top:826px;width:479px}
.about-text h2{font-family:'Montserrat',sans-serif;font-weight:700;font-size:32px;color:var(--ink)}
.about-text .kicker{margin-top:18px;font-size:14.5px;color:var(--gold);font-weight:500}
.about-text h3{margin-top:10px;font-family:'Montserrat',sans-serif;font-weight:600;font-size:20px;color:#b3585a}
.about-text .body-copy{margin-top:12px;font-size:15px;line-height:25.5px}
.about-btn{margin-top:17px;height:46px;padding:0 28px;background:var(--gold)}

/* modules */
.modules-head{left:0;top:1428px;width:1200px}
.modules-head .rule{margin-top:12px}
.modules-head .tagline{margin-top:17px}
.modules-copy{left:107px;top:1556px;width:439px}
.modules-art{left:608px;top:1560px;width:470px;height:281px;border-radius:14px;background:linear-gradient(160deg,#fafafa,#ececec);box-shadow:0 2px 14px rgba(0,0,0,.12);border:3px solid #fff}

/* red band */
.band{left:0;top:1933px;width:1200px;height:276px;background:linear-gradient(90deg,#d80a0a,#e30b0b 50%,#d80a0a)}
.band h2{color:var(--white)}
.band .rule{background:var(--gold);margin-top:8px}
.band-copy{left:190px;top:2066px;width:820px;text-align:center;color:var(--white);font-size:15.5px;line-height:27.5px}

/* platform */
.platform-head{left:0;top:2286px;width:1200px}
.platform-head .rule{margin-top:11px}
.platform-head .tagline{margin-top:18px}
.platform-intro{left:165px;top:2401px;width:870px;text-align:center;font-size:15px;line-height:27px}
.platform-art{left:163px;top:2486px;width:363px;height:375px;border:1px solid #ddd;background:linear-gradient(180deg,#ffffff,#f4f4f4)}
.platform-copy{left:586px;top:2543px;width:451px}

/* clients */
.clients{left:0;top:2946px;width:1200px;height:284px;background:var(--beige)}
.clients .section-title{margin-top:55px}
.clients .rule{margin-top:10px}
.client-row{left:0;top:3085px;width:1200px;height:78px;display:flex;justify-content:center;align-items:center;gap:30px}
.client{display:flex;align-items:center;gap:10px;font-family:'Montserrat',sans-serif;font-weight:700;font-size:22px;color:#2a2a2a}
.client-square{width:28px;height:28px;background:#2a2a2a}
.client-sep{width:1px;height:78px;background:#ddd}
.client-badge{width:80px;height:78px;background:var(--red);border-radius:4px}

/* footer */
.footer{left:0;top:3230px;width:1200px;height:374px;background:var(--footer);color:var(--white)}
.foot-title{font-size:18.5px;font-weight:700;color:var(--white)}
.foot-title::after{content:"";display:block;width:30px;height:2px;background:var(--white);margin-top:13px}
.field{position:absolute;height:43px;border:1px solid #bbb;border-radius:2px;font-size:14px;color:var(--white);padding:13px 12px}
.submit{left:112px;top:3520px;width:131px;height:43px;background:var(--red);color:var(--white);font-size:13.5px;font-weight:700;display:flex;align-items:center;justify-content:center}
.contact-item{display:flex;align-items:center;gap:16px;font-size:14px;line-height:19px;position:absolute;left:604px;color:var(--white)}
.contact-icon{width:34px;height:34px;border-radius:50%;border:1px solid #666;display:flex;align-items:center;justify-content:center;flex:none}
.contact-icon svg{width:14px;height:14px;fill:var(--red)}
.quick{left:964px;top:3335px;list-style:none;font-size:14.5px;color:var(--white)}
.quick li{height:30px;display:flex;align-items:center;gap:18px}
.quick li::before{content:"»";color:var(--red);font-size:14px}
.copyright{left:0;top:3604px;width:1200px;height:51px;background:var(--red);color:var(--white);font-size:14px;display:flex;align-items:center;justify-content:center}
</style>
</head>
<body>

<div class="abs topbar">
  <span style="left:111px"><svg viewBox="0 0 24 24"><path d="M12 2C8 2 5 5 5 9c0 5 7 13 7 13s7-8 7-13c0-4-3-7-7-7zm0 9.5A2.5 2.5 0 1 1 12 6.5a2.5 2.5 0 0 1 0 5z"/></svg>253,Lorem ipsum dolor sit amet, consectetur adipiscing</span>
  <span style="left:783px"><svg viewBox="0 0 24 24"><path d="M6.6 10.8a15 15 0 0 0 6.6 6.6l2.2-2.2a1 1 0 0 1 1-.25 11.4 11.4 0 0 0 3.6.57 1 1 0 0 1 1 1V20a1 1 0 0 1-1 1A17 17 0 0 1 3 4a1 1 0 0 1 1-1h3.5a1 1 0 0 1 1 1c0 1.25.2 2.45.57 3.6a1 1 0 0 1-.25 1z"/></svg>+1 888 888 8888</span>
  <span style="left:942px"><svg viewBox="0 0 24 24"><path d="M2 5h20v14H2zM3 6l9 7 9-7"/></svg>info@trelvix.com</span>
</div>

<header class="abs nav">
  <div class="abs brand"><div class="brand-mark"></div><div class="brand-name">TRELVIX</div></div>
  <nav class="abs menu"><span>Home</span><span>Markets</span><span>Products</span><span>Platform</span><span>Services</span><span>Resources</span><span>About</span><span>Contact Us</span></nav>
</header>

<section class="abs hero" role="img" aria-label="Hand touching a glowing ERP network interface with business icons"></section>
<div class="abs hero-welcome">Welcome To</div>
<div class="abs hero-title">TRELVIX</div>
<div class="abs hero-sub">An infinitely composable Enterprise Applications Platform (EAP) for real estate.</div>
<div class="abs btn hero-btn">Schedule Demo <svg viewBox="0 0 24 24"><circle cx="12" cy="12" r="11" fill="#fff"/><path d="M10 7l5 5-5 5" stroke="#e30b0b" stroke-width="3" fill="none"/></svg></div>

<section class="abs about"></section>
<div class="abs about-art" role="img" aria-label="Large brand emblem of stacked cubes"></div>
<div class="abs about-text">
  <h2>ABOUT US</h2>
  <div class="kicker">One Solution - Infinite Possibilities</div>
  <h3>Trelvix Enterprise</h3>
  <div class="body-copy">
    <p>Trelvix was born from decades of real estate enterprise software development and implementation experience — spanning hundreds of blue chip global real estate investment firms. But Trelvix is unlike anything you’ve experienced before.</p>
    <p>No more multi-million-dollar disruptive implementations. No more waiting for upgrades and enhancements that never come. No more trailing projects and disappointing customizations. No more settling for less than exactly what you want.</p>
  </div>
  <div class="btn about-btn">Learn More <svg viewBox="0 0 24 24"><circle cx="12" cy="12" r="11" fill="#fff"/><path d="M10 7l5 5-5 5" stroke="#d6a351" stroke-width="3" fill="none"/></svg></div>
</div>

<div class="abs modules-head">
  <h2 class="section-title">The Modules of TRX (aka Platform?)</h2>
  <div class="rule"></div>
  <div class="tagline">Simple - Secure - Scalable</div>
</div>
<div class="abs modules-copy body-copy">
  <p>Trelvix is the real estate industry’s only infinitely composable Enterprise Applications Platform (EAP), ensuring scalability, security, auditability, and compliance. Trelvix is a complete solution covering all functional areas of real estate investment, development, finance, accounting, management and operations.</p>
  <p>No more business disruption, downtime, high costs, diminishing ROI, and inflexibility. Run your business your way, break the cycle of technical debt, and focus on high-value, innovative opportunities.</p>
</div>
<div class="abs modules-art" role="img" aria-label="Software modules arranged as a periodic table of 3D blocks in teal, orange and grey"></div>

<section class="abs band">
  <h2 class="section-title" style="margin-top:63px">About Us</h2>
  <div class="rule"></div>
</section>
<div class="abs band-copy">Trelvix is the real estate industry’s modern alternative to rigid, legacy ERP systems. With decades of real estate enterprise software development and implementation expertise — spanning hundreds of blue chip global real estate investment firms — we have a proven track record of enterprise excellence.</div>

<div class="abs platform-head">
  <h2 class="section-title">Platform</h2>
  <div class="rule"></div>
  <div class="tagline">Stop settling for less than exactly what you want</div>
</div>
<div class="abs platform-intro">Trelvix combines the best of all worlds in our Enterprise Applications Platform (EAP): the simplicity and scalability of custom, no-code, software and the security and confidence of a complete, SOC 2 compliant industry solution.</div>
<div class="abs platform-art" role="img" aria-label="Grid of individual module blocks in teal, green, orange and grey"></div>
<div class="abs platform-copy body-copy">
  <p>Our modular approach enables rapid innovation and re-invention of your business by casting off the shackles of legacy ERP technology and delivering a modern, agile solution that bridges the gaps for all of your real estate workflows.</p>
  <p>No more closed systems, complicated integrations, overreliance on spreadsheets, and complex or unavailable customizations. In their place is Trelvix’ robust set of preconfigured yet flexible capabilities that can be deployed as point-solutions or to compose larger business processes.</p>
</div>

<section class="abs clients">
  <h2 class="section-title">Our Clients</h2>
  <div class="rule"></div>
</section>
<div class="abs client-row">
  <div class="client"><div class="client-square"></div>Dalsworth Partners</div>
  <div class="client-sep"></div>
  <div class="client">Dalsworth National</div>
  <div class="client" style="margin-left:20px"><div class="client-badge"></div>Torvane Co-op</div>
</div>

<footer class="abs footer"></footer>
<div class="abs foot-title" style="left:111px;top:3281px">Get In Touch</div>
<div class="field" style="left:112px;top:3343px;width:175px">Name</div>
<div class="field" style="left:296px;top:3343px;width:175px">Company</div>
<div class="field" style="left:112px;top:3400px;width:175px">Email</div>
<div class="field" style="left:296px;top:3400px;width:175px">Zipcode</div>
<div class="field" style="left:112px;top:3458px;width:359px">State</div>
<div class="abs submit">SUBMIT NOW</div>

<div class="abs foot-title" style="left:604px;top:3281px">Contact Us</div>
<div class="contact-item" style="top:3338px"><div class="contact-icon"><svg viewBox="0 0 24 24"><path d="M12 2C8 2 5 5 5 9c0 5 7 13 7 13s7-8 7-13c0-4-3-7-7-7zm0 9.5A2.5 2.5 0 1 1 12 6.5a2.5 2.5 0 0 1 0 5z"/></svg></div><span>2539 ,Lorem ipsum dolor<br>sit amet consectetur</span></div>
<div class="contact-item" style="top:3390px"><div class="contact-icon"><svg viewBox="0 0 24 24"><path d="M6.6 10.8a15 15 0 0 0 6.6 6.6l2.2-2.2a1 1 0 0 1 1-.25 11.4 11.4 0 0 0 3.6.57 1 1 0 0 1 1 1V20a1 1 0 0 1-1 1A17 17 0 0 1 3 4a1 1 0 0 1 1-1h3.5a1 1 0 0 1 1 1c0 1.25.2 2.45.57 3.6a1 1 0 0 1-.25 1z"/></svg></div><span>+1 888 888 8888</span></div>
<div class="contact-item" style="top:3443px"><div class="contact-icon"><svg viewBox="0 0 24 24"><path d="M4 4h16v16H4zM8 2h8v4H8z"/></svg></div><span>123 456 7890</span></div>
<div class="contact-item" style="top:3494px"><div class="contact-icon"><svg viewBox="0 0 24 24"><path d="M2 5h20v14H2z"/></svg></div><span>info@trelvix.com</span></div>

<div class="abs foot-title" style="left:964px;top:3281px">Quick Links</div>
<ul class="abs quick">
  <li>Home</li><li>Markets</li><li>Products</li><li>Platform</li><li>Services</li><li>Resources</li><li>About</li><li>Contact Us</li>
</ul>

<div class="abs copyright">© 2024 Trelvix. All Rights Reserved</div>

</body>
</html>
```